Investigation Before Elimination

Create a very professional and eye-catching Infographic for Birch Supply that is intended to convey to retailers that they should investigate why products are NOT selling in the Birch Supply store before they apply a discount to get rid of it. The infographic should capture all of the questions they should think about before making cutting the price. See the attachment for details on wording.

Target Market(s)

Birch Supply Business Owners

Industry/Entity Type

Retail

Font styles to use
Sans Serif

Requirements
Must have
• Any product in the infographic must be home improvement related product. See our website for ideas:
https://www.birchsupply.example/?utm_source=google&utm_medium=cpc&gclid=QxwPLMnt4R2FTkBkLpwD8WXYM5n_qa3HTkvb9aJ742_9Rm-dpLzk9Tnm80vt5zXrJg0b6-Ydxk7-vNZPm-kqEtnPAwD_BwE&gclsrc=aw.ds

* Must be in Birch Supply related colors
* Must be fun, exciting, eye-catching, unique, and clever
* 1-Page preferable but no more than two standard 8-1/2"x11"
* See the attachment for details on wording.
Should not have
• N/A

```html
<!DOCTYPE html>
<html lang="en">
<head>
<meta charset="utf-8">
<title>Investigation Before Elimination – Birch Supply</title>
<link href="https://fonts.googleapis.com/css2?family=Montserrat:wght@600;800;900&family=Ubuntu:ital,wght@0,500;0,700;1,700&family=Open+Sans:ital,wght@0,400;0,600;1,700&display=swap" rel="stylesheet">
<style>
  :root {
    --brand-red: #e11b35;
    --ink: #1d1719;
    --paper: #f1f0ef;
    --backdrop: #e4e4e4;
    --muted: #7a7a7a;
    --white: #ffffff;
  }
  * { box-sizing: border-box; margin: 0; padding: 0; }
  html, body { width: 1200px; height: 1000px; overflow: hidden; background: var(--backdrop); }
  .canvas { position: relative; width: 1200px; height: 1000px; }
  .sheet {
    position: absolute; left: 212px; top: 0; width: 776px; height: 1000px;
    background: var(--paper); overflow: hidden;
    font-family: "Open Sans", Arial, sans-serif; color: var(--ink);
  }
  .shapes { position: absolute; inset: 0; width: 776px; height: 1000px; }
  .title { position: absolute; left: 0; top: 0; width: 470px; height: 200px; }
  .title text { font-family: "Montserrat", Arial, sans-serif; font-weight: 900; font-size: 57px; }
  .intro {
    position: absolute; left: 471px; top: 19px; width: 268px;
    font-size: 10.6px; line-height: 13.7px; text-align: justify; color: #2a2a2a;
  }
  .q-num, .q-text {
    position: absolute; font-family: "Ubuntu", Arial, sans-serif; font-weight: 700;
    color: var(--white); text-transform: uppercase; white-space: nowrap;
  }
  .q-num { line-height: 0.8; }
  .q-text { font-size: 13.4px; line-height: 15.2px; }
  .q-text .dark { color: var(--ink); }
  .note-mark {
    position: absolute; font-family: "Montserrat", Arial, sans-serif; font-weight: 900;
    font-size: 44px; line-height: 1; color: var(--brand-red); height: 26px; overflow: hidden;
  }
  .note {
    position: absolute; font-family: "Open Sans", Arial, sans-serif; font-style: italic;
    font-weight: 700; font-size: 8.4px; line-height: 9px; color: var(--ink);
  }
  .resources-head {
    position: absolute; left: 32px; top: 809px; font-family: "Ubuntu", Arial, sans-serif;
    font-style: italic; font-weight: 700; font-size: 19px; line-height: 20px;
  }
  .resources-rule { position: absolute; left: 32px; top: 852px; width: 341px; height: 2px; background: var(--brand-red); }
  .resource { position: absolute; top: 865px; font-size: 11.2px; line-height: 13px; }
  .resource h3 { font-family: "Open Sans", Arial, sans-serif; font-weight: 600; font-size: 12px; line-height: 13px; }
  .resource p { word-break: break-all; }
  .brand-name {
    position: absolute; left: 514px; top: 968px; font-family: "Montserrat", Arial, sans-serif;
    font-weight: 800; font-size: 12px; line-height: 16px; color: var(--brand-red);
  }
  .brand-divider { position: absolute; left: 591px; top: 961px; width: 1px; height: 31px; background: #b5b5b5; }
  .department { position: absolute; left: 601px; top: 955px; font-family: "Montserrat", Arial, sans-serif; font-weight: 600; }
  .department .line1 { font-size: 14.5px; line-height: 16px; color: var(--muted); }
  .department .line2 { font-size: 20.5px; line-height: 22px; color: var(--brand-red); }
</style>
</head>
<body>
<div class="canvas">
  <article class="sheet">
    <svg class="shapes" viewBox="0 0 776 1000" aria-hidden="true">
      <g fill="var(--brand-red)">
        <polygon points="54,219 227,213 248,269 31,259"/>
        <polygon points="399,235 600,221 580,284 385,273"/>
        <polygon points="144,323 351,306 339,418 127,412"/>
        <polygon points="505,335 699,320 708,429 495,419"/>
        <polygon points="40,486 236,473 248,606 32,598"/>
        <polygon points="300,482 485,469 502,542 285,532"/>
        <polygon points="537,544 731,529 741,642 529,632"/>
        <polygon points="277,619 482,603 492,746 266,735"/>
        <polygon points="0,954 511,954 482,1000 0,1000"/>
      </g>
    </svg>

    <svg class="title" viewBox="0 0 470 200">
      <text x="31" y="70" fill="var(--ink)" textLength="421" lengthAdjust="spacingAndGlyphs">INVESTIGATION</text>
      <text x="31" y="124" fill="var(--ink)" textLength="216" lengthAdjust="spacingAndGlyphs">BEFORE</text>
      <text x="31" y="180" fill="var(--brand-red)" textLength="358" lengthAdjust="spacingAndGlyphs">ELIMINATION</text>
    </svg>

    <p class="intro">Dead stock in your store rapidly eats away at profits, drives up the cost of doing business, and occupies valuable shelf space that would be better served by fresh and more productive products. To address this issue, a typical knee-jerk response is marking down the product and attempting to sell it at a discount. Though this is a better approach than simply hoping it sells ’one day’, applying a markdown should be used only as a last resort after sales floor investigation takes place for common execution issues that are known to hamper sales:</p>

    <!-- Question 1 -->
    <div class="q-num" style="left:60px;top:227px;font-size:36px;">1</div>
    <div class="q-text" style="left:92px;top:226px;">Is the <span class="dark">product</span><br><span class="dark">physically</span> there?</div>
    <div class="note-mark" style="left:31px;top:267px;">“</div>
    <p class="note" style="left:61px;top:274px;">One of the most typical issues is that the item<br>is no longer existent (i.e. ghost inventory).</p>

    <!-- Question 3 -->
    <div class="q-num" style="left:412px;top:243px;font-size:34px;">3</div>
    <div class="q-text" style="left:443px;top:241px;">Is the item <span class="dark">priced</span><br><span class="dark">competitively?</span></div>
    <div class="note-mark" style="left:384px;top:287px;">“</div>
    <p class="note" style="left:414px;top:292px;">In today’s price sensitive market,making<br>sure the cost of the SKU is in line with<br>the customer expectation is key.</p>

    <!-- Question 2 -->
    <div class="q-num" style="left:146px;top:334px;font-size:100px;">2</div>
    <div class="q-text" style="left:207px;top:329px;">Is the item<br><span class="dark">merchandised<br>properly</span> - is it in<br>plain view of<br>the customer?</div>
    <div class="note-mark" style="left:128px;top:419px;">“</div>
    <p class="note" style="left:157px;top:424px;">Find out if it is stuck in the backroom,<br>top stock, or buried behind other products.</p>

    <!-- Question 4 -->
    <div class="q-num" style="left:507px;top:346px;font-size:100px;">4</div>
    <div class="q-text" style="left:578px;top:341px;">Is <span class="dark">the physical<br>product and<br>packaging</span><br>in a desirable<br>condition?</div>
    <div class="note-mark" style="left:488px;top:432px;">“</div>
    <p class="note" style="left:517px;top:436px;">Bottom-line: Nobody wants ripped or torn,<br>or physically abused merchandise.</p>

    <!-- Question 5 -->
    <div class="q-num" style="left:40px;top:500px;font-size:134px;">5</div>
    <div class="q-text" style="left:117px;top:501px;">Is the item<br><span class="dark">unique enough</span><br>to where an<br>alike <span class="dark">SKU</span> isn’t<br><span class="dark">cannibalizing</span><br>its sales?</div>
    <div class="note-mark" style="left:32px;top:614px;">“</div>
    <p class="note" style="left:62px;top:619px;">Each SKU needs to be different and stand on<br>its own. Eliminate redundancies in the<br>product mix.</p>

    <!-- Question 7 -->
    <div class="q-num" style="left:312px;top:484px;font-size:64px;">7</div>
    <div class="q-text" style="left:356px;top:485px;">Is the item still<br><span class="dark">relevant</span> to<br>the shopper?</div>
    <div class="note-mark" style="left:285px;top:545px;">“</div>
    <p class="note" style="left:314px;top:550px;">Get rid of outdated product and technology...<br>those old rotary dial phone cords!</p>

    <!-- Question 8 -->
    <div class="q-num" style="left:538px;top:558px;font-size:104px;">8</div>
    <div class="q-text" style="left:601px;top:553px;">Is the sale of<br>the <span class="dark">SKU<br>independent</span><br>of the sale<br>of another item?</div>
    <div class="note-mark" style="left:521px;top:646px;">“</div>
    <p class="note" style="left:550px;top:651px;">With SKUs that depend on each other to sell,<br>analyze the sell through and performance<br>of the other item.</p>

    <!-- Question 6 -->
    <div class="q-num" style="left:278px;top:634px;font-size:134px;">6</div>
    <div class="q-text" style="left:357px;top:623px;">Do you have<br><span class="dark">enough<br>quantity</span> of the<br>item for the<br>customer to<br>want to <span class="dark">make<br>the purchase?</span></div>
    <div class="note-mark" style="left:267px;top:752px;">“</div>
    <p class="note" style="left:297px;top:757px;">Each SKU needs to be different and stand on<br>its own. Eliminate redundancies in the<br>product mix.</p>

    <h2 class="resources-head">For further detail on in-stock position,<br>see the following resources:</h2>
    <div class="resources-rule"></div>

    <section class="resource" style="left:32px;width:226px;">
      <h3>Obsolete Inventory-<br>Closeout Management (COM) Setup</h3>
      <p>https://portal.birchsupply.example/awor/ inventory-management/obsolete-inventory -closeout-management-(com)-setup</p>
    </section>
    <section class="resource" style="left:320px;width:196px;">
      <h3>In-Stock Procedures</h3>
      <p>https://portal.birchsupply.example/ awor/inventory-management/ obsolete-inventory-closeout- management-(com)-store-procedures</p>
    </section>
    <section class="resource" style="left:579px;width:166px;">
      <h3>Markdown Strategy</h3>
      <p>https://portal.birchsupply.example /awor/inventory-management/ markdown-strategy</p>
    </section>

    <div class="brand-name">Birch Supply</div>
    <div class="brand-divider"></div>
    <div class="department">
      <div class="line1">STORE SYSTEMS &amp;</div>
      <div class="line2">OPERATIONS</div>
    </div>
  </article>
</div>
</body>
</html>
```